Velbrook Heating Business Card Design

Design new, 2 sides, business cards for a residential and light commercial heating, air conditioning contractor.

Target Market(s)

Homeowners, small businesses

Industry/Entity Type

Business

Contact Information for Business Card

Dominic Westerhall
Phone - 862-415-2736
Email
Address - PO box 518
Brightwater NJ 07912
Website - www.HarborBreezeLLC.example

Requirements
Must have
• logo, company colors, standard size with no die cut, so I can use nova stamp

```html
<!DOCTYPE html>
<html lang="en">
<head>
<meta charset="utf-8">
<title>Velbrook Heating Business Card</title>
<link rel="stylesheet" href="https://fonts.googleapis.com/css2?family=Open+Sans:wght@400;600&display=swap">
<style>
  :root {
    --brand-red: #9e2133;
    --cream: #fbe7b5;
    --ink: #2a2a2a;
    --paper: #ffffff;
    --backdrop: #ece8e4;
  }
  * { margin: 0; padding: 0; box-sizing: border-box; }
  html, body { width: 1200px; height: 900px; overflow: hidden; }
  body {
    position: relative;
    background: var(--backdrop);
    font-family: "Open Sans", Arial, sans-serif;
    color: var(--ink);
  }
  .card {
    position: absolute;
    box-shadow: 0 4px 14px rgba(0,0,0,0.18);
  }
  .card--front {
    left: 77px; top: 35px; width: 589px; height: 363px;
    background: var(--paper);
  }
  .card--back {
    left: 388px; top: 505px; width: 566px; height: 352px;
    background: var(--brand-red);
  }
  .front-bands { position: absolute; left: 0; top: 103px; }
  .brand-name {
    position: absolute;
    font-weight: 600;
    white-space: nowrap;
    transform: translateX(-50%);
  }
  .card--front .brand-name {
    left: 295px; top: 111px;
    font-size: 34px; line-height: 44px;
    color: var(--brand-red);
  }
  .card--back .brand-name {
    left: 283px; top: 148px;
    font-size: 40px; line-height: 52px;
    color: var(--cream);
  }
  .holder { position: absolute; left: 34px; top: 238px; }
  .holder__name {
    font-size: 19px; font-weight: 600; color: var(--brand-red); line-height: 26px;
  }
  .holder__title, .holder__address {
    font-size: 15px; line-height: 21px;
  }
  .holder__address { margin-top: 4px; }
  .contact-list {
    position: absolute; right: 36px; top: 245px;
    list-style: none; text-align: right;
    font-size: 15px; line-height: 21px;
  }
  .contact-list li { display: flex; justify-content: flex-end; align-items: center; gap: 6px; }
  .contact-list svg { width: 11px; height: 11px; fill: var(--brand-red); }
</style>
</head>
<body>
  <section class="card card--front" aria-label="Business card front">
    <svg class="front-bands" width="589" height="60" viewBox="0 0 589 60" aria-hidden="true">
      <polygon points="0,0 128,0 141,30 128,60 0,60" fill="var(--brand-red)"/>
      <polygon points="461,0 589,0 589,60 461,60 451,30" fill="var(--brand-red)"/>
    </svg>
    <div class="brand-name">Velbrook Heating</div>

    <div class="holder">
      <p class="holder__name">Dominic Westerhall</p>
      <p class="holder__title">Managing Director</p>
      <p class="holder__address">PO box 518<br>Brightwater NJ 07912</p>
    </div>

    <ul class="contact-list">
      <li>862-415-2736
        <svg viewBox="0 0 12 12" aria-label="phone"><path d="M2.5 0.5l2 2-1 1.5c.7 1.6 2 2.9 3.5 3.5l1.5-1 2 2-1.3 1.8C5.5 10 2 6.5 0.7 1.8z"/></svg>
      </li>
      <li>862-415-2737
        <svg viewBox="0 0 12 12" aria-label="fax"><path d="M3 0h5l1 1v3h2v8H1V4h2zM4 1v3h4V1.5zM3 6v1.5h2V6zm3.5 0v1.5h2V6zM3 8.5V10h2V8.5zm3.5 0V10h2V8.5z"/></svg>
      </li>
      <li>info@velbrook.example
        <svg viewBox="0 0 12 12" aria-label="email"><path d="M0 2h12v8H0zM1 3l5 3.5L11 3z" fill-rule="evenodd"/></svg>
      </li>
      <li>www.VelbrookHeatingLLC.example
        <svg viewBox="0 0 12 12" aria-label="website"><path d="M6 0a6 6 0 100 12A6 6 0 006 0zm0 1c.8.8 1.4 2.2 1.5 4.5h-3C4.6 3.2 5.2 1.8 6 1zM1.1 5.5a5 5 0 012.6-4c-.6 1.1-1 2.5-1.1 4zm0 1h1.5c.1 1.5.5 2.9 1.1 4a5 5 0 01-2.6-4zm3.4 0h3C7.4 8.8 6.8 10.2 6 11c-.8-.8-1.4-2.2-1.5-4.5zm4.9 0h1.5a5 5 0 01-2.6 4c.6-1.1 1-2.5 1.1-4zm0-1c-.1-1.5-.5-2.9-1.1-4a5 5 0 012.6 4z"/></svg>
      </li>
    </ul>
  </section>

  <section class="card card--back" aria-label="Business card back">
    <div class="brand-name">Velbrook Heating</div>
  </section>
</body>
</html>
```